Residential Mortgage Leader needs Wordpress Design

Looking for a home page website design for a client. We develop using the WordPress platform and would prefer the design be at least loosely based on an existing WordPress template. Attached files have many notes from our creative brief with client. The site must be responsive. Approved, basic wireframe attached. There is room for interpretation.

Existing web site: http://www.marisolkettering.example/

The Marisol Kettering Team relies on strong systems to deliver an on-time, done-right, friendly experience. Marisol offers mortgages and refinancing services throughout the United States. She is a successful Brookvale Funding agent who strives to be an active part of her community. She would like to focus the site on her team, rather than just her.

Difference makers...
When you work with the Marisol Kettering team you get a high level of expertise and a friendly experience.

She has amazing credentials. Marisol is widely recognized as a top producer for her company, and has earned a number of awards and honors for her customer service.

Marisol's team is very engaged and enjoys sharing social comments or photos from their community.

Imagery:
* Friendly, warm imagery, preferably of her team or an image to represent her team
* Clean and crisp
* Professional / Experts in mortgage and refinance
* Clean / Good use of white space
Updates

When possible, please use imagery from the DFW area. The client mentioned they would prefer not to see stock images. Thanks.

Amend that- creative use of stock images, however, is fine. A few designs have used stock imagery, but in a well-considered manner.

We added some photos and graphics that are local. We are Dallas / Ft. Worth, Plano, Frisco, Texas. We also added some examples of photos to use for the "In the Community" area. Stock photos of business folks just doesn't fit there. Thanks!

Target Market(s)

They service a lot of builders, but also work with homeowners. Their typical client is usually a woman searching for mortgage services online. She typically has a family and may refer her husband to Marisol's team. Keep in mind, however, they also see a number of other scenarios. Most of their clients are middle to high-end borrowers.

Industry/Entity Type

It Company

Requirements
Must have
• Design should be developed using program such as Photoshop or Fireworks or Illustrator as last preference. Ideally, the design would be based on an existing responsive WordPress theme, which we would customize. You must include the name of the target theme. The footer should include lots of space for disclaimers and legal language. Site navigation should include these choices: "Home, About, Builders, Mortgage Info, Approval, Blog, Contact"
Nice to have
• Blog, social media and photos area. Use of the already approved style prototype with colors and fonts (Lato- a Google font, Times New Roman and Cookie-a decorative Google font). However, we are open to interpretation.
Should not have
• Hard to read fonts or a lack of white space.

```html
<!DOCTYPE html>
<html lang="en">
<head>
<meta charset="utf-8">
<title>Brookvale Funding – Marisol Kettering Team</title>
<link rel="stylesheet" href="https://fonts.googleapis.com/css2?family=Lato:wght@400;700&family=Cookie&family=Tinos&display=swap">
<style>
:root{
  --brand-red:#c23a22;
  --brand-blue:#1a82b5;
  --button-blue:#2b8fcd;
  --ink:#2b2b2b;
  --muted:#b4b4b4;
  --hero-bg:#f3f3f3;
  --footer-bg:#363636;
  --footer-base:#2c2c2c;
  --footer-text:#d9d9d9;
  --line:#e2e2e2;
}
*{margin:0;padding:0;box-sizing:border-box}
html,body{width:1022px;height:1200px;overflow:hidden;background:#fff}
body{font-family:"Lato",Arial,sans-serif;color:var(--ink)}
.page{position:relative;width:1200px;height:1409px;transform:scale(.851667);transform-origin:0 0}
.abs{position:absolute}
.serif{font-family:"Tinos","Times New Roman",serif}

/* header */
.top-bar{left:0;top:0;width:1200px;height:6px;background:var(--brand-red)}
.header{left:0;top:6px;width:1200px;height:121px;background:#fff;border-bottom:1px solid var(--line)}
.brand{left:128px;top:48px;display:flex;align-items:center;gap:12px}
.brand-name{font-size:30px;font-weight:700;color:var(--brand-red);letter-spacing:-.5px}
.brand-dot{width:26px;height:26px;border-radius:50%;background:var(--brand-red)}
.brand-sub{left:128px;top:85px;font-size:15px;font-weight:700;color:#555}
.nav-active{left:541px;top:6px;width:84px;height:121px;background:#f5f5f5;border-bottom:4px solid var(--brand-red)}
.nav{top:55px;font-size:15px;color:#333}

/* hero */
.hero{left:0;top:127px;width:1200px;height:404px;background:var(--hero-bg);border-bottom:1px solid var(--line)}
.hero-title{left:128px;top:166px;font-family:"Cookie",cursive;font-size:50px;color:var(--brand-blue)}
.hero-copy{left:128px;width:375px;font-size:13px;line-height:18px;color:#222}
.hero-btn{left:128px;top:443px;width:152px;height:45px;background:var(--button-blue);border:1px solid #1c78b0;color:#fff;font-size:19px;display:flex;align-items:center;justify-content:center}
.hero-photo{left:521px;top:181px;width:548px;height:306px;border:1px solid #ddd;background:linear-gradient(120deg,#6d5a44 0%,#b98a63 35%,#e3c2a4 55%,#8aa08f 70%,#5a4a3a 100%)}

/* features */
.feature-icon{width:58px;height:58px;border-radius:50%;background:var(--brand-red);display:flex;align-items:center;justify-content:center}
.feature-title{font-size:25px;color:var(--brand-red)}
.feature-text{font-size:13px;line-height:18px;color:#222}
.divider{left:0;width:1178px;height:2px;background:var(--button-blue)}

/* lower */
.section-title{top:800px;font-size:23px;color:var(--brand-blue)}
.post-title{left:128px;font-size:18px;color:#222}
.post-text{left:128px;width:260px;font-size:13px;line-height:18px;color:var(--muted)}
.social-box{left:469px;width:55px;height:52px;border:1px solid #e4e4e4;background:#fafafa;display:flex;align-items:center;justify-content:center}
.social-name{left:540px;font-size:18px;color:#222}
.social-text{left:540px;font-size:13px;color:var(--muted)}
.tile{width:88px;height:81px;border:1px solid #e3e3e3}

/* footer */
.footer{left:0;top:1046px;width:1200px;height:295px;background:var(--footer-bg)}
.footer-base{left:0;top:1341px;width:1200px;height:68px;background:var(--footer-base)}
.portrait{left:129px;top:1104px;width:146px;height:166px;border:1px solid #555;background:linear-gradient(160deg,#5b5149,#8a6c58 55%,#3e3731)}
.f-name{left:284px;top:1101px;font-size:18px;line-height:22px;color:#fff}
.f-list{font-size:13px;line-height:23px;color:var(--footer-text)}
.f-head{top:1102px;font-size:17px;color:#fff}
.lang{left:845px;top:1292px;width:108px;height:33px;background:#262626;color:#ddd;font-size:13px;display:flex;align-items:center;padding-left:10px;gap:12px}
.copy{left:130px;top:1367px;font-size:13px;color:var(--footer-text)}
.sq{top:1362px;width:33px;height:33px;border-radius:3px}
</style>
</head>
<body>
<div class="page">
  <div class="abs top-bar"></div>
  <header class="abs header"></header>
  <div class="abs brand"><span class="brand-name">Brookvale Funding</span><span class="brand-dot"></span></div>
  <div class="abs brand-sub">A Harborline Capital Company</div>

  <div class="abs nav-active"></div>
  <nav>
    <span class="abs nav" style="left:560px">Home</span>
    <span class="abs nav" style="left:639px">About Us</span>
    <span class="abs nav" style="left:729px">Buliders</span>
    <span class="abs nav" style="left:812px">Mortgage Info</span>
    <span class="abs nav" style="left:937px">Blog</span>
    <span class="abs nav" style="left:993px">Contact Us</span>
  </nav>

  <section class="abs hero"></section>
  <h1 class="abs hero-title" style="font-weight:400">Earning Your Business</h1>
  <p class="abs hero-copy" style="top:240px">Lorem ipsum dolor sit amet, consectetur adipisicing elit, sed do eiusmod tempor incididunt ut labore et dolore magna aliqua.</p>
  <p class="abs hero-copy" style="top:312px">&nbsp;Ut enim ad minim veniam, quis nostrud exercitation ullamco laboris nisi ut aliquip ex ea commodo consequat. Duis aute irure dolorpariatur.</p>
  <p class="abs hero-copy" style="top:384px">Excepteur sint occaecat cupidatat non proident, sunt in culpa qui officia deserunt mollit anim id est laborum.</p>
  <div class="abs hero-btn serif">Get to Know Us</div>
  <div class="abs hero-photo" role="img" aria-label="Hands holding a small model house"></div>

  <!-- features -->
  <div class="abs feature-icon" style="left:128px;top:590px"><svg width="30" height="26" viewBox="0 0 30 26"><circle cx="10" cy="8" r="5" fill="#fff"/><circle cx="20" cy="8" r="5" fill="#fff"/><rect x="2" y="15" width="26" height="10" rx="4" fill="#fff"/></svg></div>
  <div class="abs feature-title serif" style="left:194px;top:606px">Our Credentials</div>
  <p class="abs feature-text" style="left:195px;top:644px;width:318px">Lorem ipsum dolor sit amet, consectetur adipisicing elit, sed do eiusmod tempor incididunt ut labore et dolore magna aliqua...</p>

  <div class="abs feature-icon" style="left:521px;top:590px"><svg width="30" height="28" viewBox="0 0 30 28"><circle cx="15" cy="7" r="5" fill="#fff"/><circle cx="8" cy="18" r="5" fill="#fff"/><circle cx="22" cy="18" r="5" fill="#fff"/></svg></div>
  <div class="abs feature-title serif" style="left:588px;top:606px">Awards</div>
  <p class="abs feature-text" style="left:588px;top:644px;width:200px">Lorem ipsum dolor sit amet con-sectetur adipsicing elit sed do euismod...</p>

  <div class="abs feature-icon" style="left:802px;top:590px"><svg width="30" height="30" viewBox="0 0 30 30" fill="none" stroke="#fff" stroke-width="2.5"><circle cx="15" cy="15" r="12"/><circle cx="15" cy="15" r="7"/><circle cx="15" cy="15" r="2" fill="#fff"/></svg></div>
  <div class="abs feature-title serif" style="left:868px;top:606px">Recognion</div>
  <p class="abs feature-text" style="left:869px;top:644px;width:200px">Lorem ipsum dolor sit amet con-sectetur adipsicing elit sed do euismod...</p>

  <div class="abs divider" style="top:756px"></div>
  <div class="abs divider" style="top:760px"></div>

  <!-- blog -->
  <h2 class="abs section-title serif" style="left:128px;font-weight:400">Blog</h2>
  <div class="abs post-title" style="top:842px">• Bomowing</div>
  <p class="abs post-text" style="top:868px">Sed ut perspiciatis unde omnis iste natus error sit voluptatem accusantium dolo-remque laudantium...</p>
  <div class="abs post-title" style="top:934px">• Best Practices</div>
  <p class="abs post-text" style="top:960px">Sed ut perspiciatis unde omnis iste natus error sit voluptatem accusantium dolo-remque laudantium...</p>

  <!-- social -->
  <h2 class="abs section-title serif" style="left:469px;font-weight:400">Social Icons</h2>
  <div class="abs social-box" style="top:844px"><svg width="18" height="18"><rect width="18" height="18" rx="3" fill="#555"/></svg></div>
  <div class="abs social-name" style="top:846px">Community Page</div>
  <div class="abs social-text" style="top:875px">Lorem ipsum dolor sit amet...</div>
  <div class="abs social-box" style="top:904px"><svg width="18" height="18"><rect width="18" height="18" rx="3" fill="#555"/></svg></div>
  <div class="abs social-name" style="top:906px">Quick Updates</div>
  <div class="abs social-text" style="top:935px">Lorem ipsum dolor sit amet...</div>
  <div class="abs social-box" style="top:964px"><svg width="26" height="26" viewBox="0 0 26 26" fill="none" stroke="#555" stroke-width="3.5"><circle cx="4" cy="22" r="2.5" fill="#555" stroke="none"/><path d="M2 12a12 12 0 0 1 12 12"/><path d="M2 3a21 21 0 0 1 21 21"/></svg></div>
  <div class="abs social-name" style="top:966px">Rss</div>
  <div class="abs social-text" style="top:995px">Lorem ipsum dolor sit amet...</div>

  <!-- community -->
  <h2 class="abs section-title serif" style="left:792px;font-weight:400">In The Community</h2>
  <div class="abs tile" style="left:792px;top:844px;background:linear-gradient(#6aa6d6,#e0b07a)" role="img" aria-label="Group of neighbours together"></div>
  <div class="abs tile" style="left:888px;top:844px;background:linear-gradient(#3d7fb7,#9b8a7a)" role="img" aria-label="Team members outdoors"></div>
  <div class="abs tile" style="left:984px;top:844px;background:linear-gradient(#c9c4bd,#8a5e52)" role="img" aria-label="Team at a local building"></div>
  <div class="abs tile" style="left:792px;top:934px;background:linear-gradient(#e8e5e0,#b39b82)" role="img" aria-label="Friends in a circle"></div>
  <div class="abs tile" style="left:888px;top:934px;background:linear-gradient(#d68f61,#c5533c)" role="img" aria-label="Hands joined together"></div>
  <div class="abs tile" style="left:984px;top:934px;background:linear-gradient(#f0efeb,#7aa15d)" role="img" aria-label="Young people celebrating"></div>

  <!-- footer -->
  <footer class="abs footer"></footer>
  <div class="abs portrait" role="img" aria-label="Portrait of the branch manager"></div>
  <div class="abs f-name">Marisol Kettering<br>Branch Manager</div>
  <div class="abs f-list" style="left:285px;top:1151px">Office: 469.555.0148<br>Cell: 866.555.0172<br>mkettering@brookvalefunding.example<br>NMLS: 48215<br>2280 Cedar Commons , Ste. 140<br>Alder Springs, TX 75990</div>
  <div class="abs f-list" style="left:285px;top:1312px;color:#fff">Directions</div>

  <div class="abs f-head" style="left:579px">LINKS</div>
  <div class="abs f-list" style="left:580px;top:1141px">Home<br>About<br>Builders<br>Mortgage Info<br>Approval<br>Blog<br>Contact Us</div>

  <div class="abs f-head" style="left:844px">ADDRESS</div>
  <div class="abs f-list" style="left:845px;top:1141px">Our Address<br>Corporate Office - 4400 Linden Parkway,<br>Suite 700 Alder Springs, Texas 75991<br><br>Tel : 1-800-555-0142<br>Email : Contact Brookvale Funding</div>
  <div class="abs lang">Language... <svg width="10" height="6" viewBox="0 0 10 6"><path d="M1 1l4 4 4-4" fill="none" stroke="#ddd" stroke-width="1.5"/></svg></div>

  <div class="abs footer-base"></div>
  <div class="abs copy">Copyright © 2013 Brookvale Funding. All Rights Reserved</div>
  <div class="abs sq" style="left:907px;background:#5fb6dc"></div>
  <div class="abs sq" style="left:945px;background:#4a6aa5"></div>
  <div class="abs sq" style="left:984px;background:#e2772a"></div>
  <div class="abs sq" style="left:1030px;border:2px solid #ddd;border-radius:2px"></div>
</div>
</body>
</html>
```